Association qui souhaite améliorer l'accès aux personnes en situation de handicap

Nous sommes une association qui a pour objectif d'améliorer l'accessibilité, augmenter l'offre des activités réalisables dans notre région touristique.
Nous souhaitons réaliser un site internet afin de pouvoir communiquer sur notre association. Nous avons déjà conçu notre flyer sur Plumotrix. Nous souhaiterions une base graphique se rapportant à celui-ci. C'est possible de tout retravailler mais nous souhaitons tout de même retrouver la charte graphique ou code couleur du flyer.
Il nous faudrait quelques pages:
- 1 page : Acceuil / Présentation (Home), Il y aurait le descriptif de l'association, avec ses objectifs à +/- moyen terme
- 1 page : Nos réalisations, celle-ci présenterait les éléments que nous avons réalisés avec des zones de textes et des images classées chronologiquement au fur et à mesure des nouveautés
- 1 page : Media, comme la précédente, mais ou on pourrait voir ou lire sur les divers médias qui parlent de nous
- 1 page : Evenements : c'est une page pour présenter divers activités que nous allons organiser
- 1 page : Contact qui indique comment nous contacter et avec la présentation des 5 ou 6 membres du comité
- 1 link donate : qui arrive sur un formulaire de donnée que l'on pourra faire évoluer sur un système de payement par la suite. Cette bannière doit se retrouver sur toutes les pages
Il est nécessaire que se design puisse être transféré sur une lecture sur téléphone mobile
Personnes en situation de handicap
Associatif

```html
<!DOCTYPE html>
<html lang="en">
<head>
<meta charset="utf-8">
<title>OpenPath Association</title>
<link rel="stylesheet" href="https://fonts.googleapis.com/css2?family=Bebas+Neue&family=Montserrat:wght@600;700;800&family=Raleway:wght@400;500;600;700&display=swap">
<style>
:root{
  --red:#e0141e;
  --red-dark:#b50d16;
  --ink:#1f1f1f;
  --text:#3a3a3a;
  --grey-bg:#e3e4e8;
  --grey-line:#c9cacf;
  --faint:#efefef;
  --footer:#2c2c2e;
  --white:#ffffff;
}
*{margin:0;padding:0;box-sizing:border-box}
html,body{width:1200px;height:4468px;overflow:hidden;background:var(--white)}
body{font-family:"Raleway",sans-serif;color:var(--text);position:relative}
.page{position:relative;width:1200px;height:4468px;overflow:hidden}
.abs{position:absolute}
.btn{position:absolute;display:flex;align-items:center;height:40px;padding:0 22px;background:var(--red);color:var(--white);font:700 13px "Montserrat",sans-serif;letter-spacing:.3px}
.btn::after{content:"";position:absolute;right:-22px;top:0;width:18px;height:40px;background:repeating-linear-gradient(100deg,var(--red) 0 4px,transparent 4px 8px)}
.heading{font-family:"Bebas Neue",sans-serif;color:var(--ink);font-size:46px;line-height:48px;border-left:3px solid var(--red);padding-left:16px}
.big-num{font-family:"Montserrat",sans-serif;font-weight:800;color:var(--faint);font-size:230px;line-height:1;letter-spacing:-10px}
.bullets{list-style:none}
.bullets li{position:relative;padding-left:38px;font-size:13.5px;line-height:24px;margin-bottom:24px;color:var(--text)}
.bullets li::before{content:"";position:absolute;left:0;top:5px;width:24px;height:14px;border:2px solid var(--red);border-right:none;clip-path:polygon(0 0,100% 100%,0 100%)}
/* header */
.header{position:absolute;left:0;top:0;width:1200px;height:83px;background:var(--white);border-top:3px solid var(--red)}
.brand{position:absolute;display:flex;align-items:center;gap:10px;font:800 22px "Montserrat",sans-serif;color:var(--ink)}
.brand .mark{width:22px;height:22px;background:var(--red)}
.email{left:582px;top:9px;font:700 15px "Montserrat",sans-serif;color:var(--ink);display:flex;align-items:center;gap:8px;white-space:nowrap}
.email .dot{width:26px;height:26px;border-radius:50%;background:var(--red)}
.donate{position:absolute;left:942px;top:0;width:86px;height:40px;background:var(--red);color:#fff;font:700 14px "Montserrat",sans-serif;display:flex;align-items:center;justify-content:center}
.donate::after{content:"";position:absolute;right:-26px;top:0;width:22px;height:40px;background:repeating-linear-gradient(100deg,var(--red) 0 4px,transparent 4px 8px)}
.nav{position:absolute;top:56px;left:463px;display:flex;gap:45px;font:600 13px "Montserrat",sans-serif;color:var(--ink)}
.nav .lang{display:flex;align-items:center;gap:8px}
.nav .flag{width:24px;height:14px;background:#1f3f8c;border:1px solid #ccc}
/* hero */
.hero-title{left:262px;top:140px;font:800 56px/52px "Montserrat",sans-serif;color:var(--ink);display:flex;flex-direction:column}
.hero-text{left:263px;top:265px;width:470px;font:600 19px/28px "Raleway",sans-serif;color:var(--ink)}
/* events */
.event-card{left:144px;top:2686px;width:426px;height:402px;background:linear-gradient(180deg,#8a7d70 0%,#7a2a2e 45%,#3c1114 100%)}
.event-card .date{position:absolute;left:40px;top:290px;font:400 26px "Bebas Neue",sans-serif;color:var(--red)}
.event-card .ttl{position:absolute;left:40px;top:328px;font:700 13px "Montserrat",sans-serif;color:#fff}
.event-card .sub{position:absolute;left:40px;top:352px;font:500 12px "Raleway",sans-serif;color:#eee}
.event-card .plus{position:absolute;right:20px;bottom:30px;width:26px;height:26px;border-radius:50%;background:var(--red);color:#fff;font:700 18px/26px sans-serif;text-align:center}
.event-item{position:absolute;left:577px;width:481px;height:112px}
.event-item .box{position:absolute;left:52px;top:0;right:0;height:112px;border:2px solid #d4d4d4;background:#fff;padding:22px 22px 0 60px}
.event-item .box h4{font:700 13px "Montserrat",sans-serif;color:var(--ink);margin-bottom:12px}
.event-item .box p{font:400 12.5px/23px "Raleway",sans-serif;color:#666}
.event-item .diamond{position:absolute;left:8px;top:10px;width:92px;height:92px}
.event-item .day{position:absolute;left:8px;top:22px;width:92px;text-align:center;font:400 28px/28px "Bebas Neue",sans-serif;color:#fff}
.arrows{left:957px;top:2590px;display:flex;gap:12px}
.arrows span{width:42px;height:42px;border:2px solid #555;border-radius:50%;display:flex;align-items:center;justify-content:center}
/* membership */
.member{left:760px;top:3325px;color:#fff}
.member h3{font:800 22px/28px "Montserrat",sans-serif;margin-bottom:8px}
.member p{font:700 12.5px/28px "Montserrat",sans-serif}
/* contact */
.field{position:absolute;border:2px solid #bdbdbd;background:#fff;font:500 13px "Raleway",sans-serif;color:#666;padding:14px 20px}
/* footer */
.footer{left:0;top:4304px;width:1200px;height:164px;background:var(--footer);color:#fff}
.footer .brand{left:156px;top:54px;color:#fff;font-size:26px}
.footer .addr{position:absolute;left:572px;top:50px;font:700 14px "Raleway",sans-serif;display:flex;align-items:center;gap:10px}
.footer .social{display:flex;gap:10px;margin-left:22px}
.footer .social span{width:26px;height:26px;border-radius:50%;background:#2f7fd8}
.footer .copy{position:absolute;left:572px;top:104px;font:500 13px "Raleway",sans-serif;color:#ddd}
</style>
</head>
<body>
<div class="page">

  <div class="abs" style="left:0;top:83px;width:1200px;height:840px;background:#ececec"></div>
  <div class="abs" role="img" aria-label="Photo of a smiling woman and girl working together at a laptop" style="left:560px;top:83px;width:640px;height:660px;background:linear-gradient(120deg,#d9d9d9 0%,#c9b7a6 40%,#e6d8ca 70%,#cfd3d8 100%)"></div>
  <svg class="abs" style="left:0;top:83px" width="1200" height="840" viewBox="0 83 1200 840">
    <polygon points="0,330 530,916 1200,711 1200,923 0,923" fill="#ffffff"/>
    <polygon points="0,245 0,330 530,916 1200,711 1200,588 560,900" fill="#e0141e"/>
    <polygon points="530,916 1200,711 1200,725 545,918" fill="#ffffff"/>
    <circle cx="746" cy="792" r="32" fill="#ffffff" stroke="#eeeeee" stroke-width="6"/>
    <path d="M746 778 V804 M737 795 L746 804 L755 795" stroke="#1f1f1f" stroke-width="3" fill="none"/>
  </svg>

  <header class="header">
    <div class="brand" style="left:142px;top:20px"><span class="mark"></span>OpenPath Association</div>
    <div class="abs email"><span class="dot"></span>info@openpath-association.example</div>
    <div class="donate">DONATE</div>
    <nav class="nav">
      <span>HOME</span><span>OUR ACHIEVEMENTS</span><span>MEDIA</span><span>EVENTS</span><span>CONTACT</span>
      <span class="lang"><span class="flag"></span>▾</span>
    </nav>
  </header>

  <h1 class="abs hero-title"><span>OPENPATH</span><span>ASSOCIATION</span></h1>
  <p class="abs hero-text">Friends living in the region who care to make the Dents du Midi region the most possible accessible to people in disability status.</p>
  <a class="btn" style="left:264px;top:378px;height:38px">GET STARTED</a>

  <div class="abs big-num" style="left:8px;top:720px">01</div>
  <div class="abs" style="left:160px;top:898px;font:600 13px 'Montserrat',sans-serif;color:var(--red)">ABOUT</div>
  <h2 class="abs heading" style="left:142px;top:954px;width:300px">PROJECTS AND<br>ASSOCIATIONS</h2>
  <ul class="abs bullets" style="left:160px;top:1076px;width:420px">
    <li>Promote the reception and leisure of people with disabilities in the Dents du Midi region by bringing together the information</li>
    <li>To serve the general interest of people in disability as well as relieve caregivers and companions.</li>
    <li>Allow access to leisure and places like everyone else.</li>
    <li>Raising awareness and changing social representations, through actions, communications, projects and events touching and involving partners associative, economic, political, media and the general public.</li>
    <li>Promote collaboration with local actors.</li>
  </ul>
  <a class="btn" style="left:143px;top:1486px;height:42px">READ MORE</a>

  <svg class="abs" style="left:600px;top:940px" width="600" height="610" viewBox="600 940 600 610">
    <line x1="962" y1="958" x2="1188" y2="1258" stroke="#e0141e" stroke-width="18"/>
    <line x1="622" y1="1272" x2="848" y2="1525" stroke="#e0141e" stroke-width="18"/>
    <polygon role="img" aria-label="Photo of a hand holding grass in a sunlit field" points="905,1075 1140,1300 915,1525 675,1300" fill="#7f9560" stroke="#fff" stroke-width="6"/>
    <polygon role="img" aria-label="Photo of a girl blowing a dandelion" points="785,955 900,1070 785,1185 670,1070" fill="#4b6b8f" stroke="#fff" stroke-width="6"/>
    <polygon role="img" aria-label="Photo of a man walking with a cane outdoors" points="1010,1265 1140,1395 1010,1525 880,1395" fill="#a8b07a" stroke="#fff" stroke-width="6"/>
  </svg>

  <svg class="abs" style="left:0;top:1600px" width="1200" height="875" viewBox="0 1600 1200 875">
    <polygon points="0,1786 326,1604 572,1847 818,1604 1200,1821 1200,2475 0,2475" fill="#c9cacf"/>
    <polygon points="0,1812 326,1632 572,1875 818,1632 1200,1848 1200,2475 0,2475" fill="#e3e4e8"/>
    <path d="M120 1960 C200 1880 380 1870 500 1920 C600 1965 590 2150 540 2250 C480 2370 330 2400 200 2365 C80 2330 10 2220 30 2120 C45 2050 70 2010 120 1960 Z" fill="#e0141e"/>
    <path role="img" aria-label="Photo of a man operating a camera stabilizer" d="M190 1935 C290 1900 420 1905 500 1955 C560 2000 548 2140 515 2230 C470 2330 360 2350 250 2325 C150 2300 70 2220 75 2120 C80 2040 120 1965 190 1935 Z" fill="#8f9b7e"/>
  </svg>
  <div class="abs big-num" style="left:845px;top:2255px">02</div>
  <h2 class="abs heading" style="left:610px;top:1930px;width:470px">EXAMPLES CONCERTS OF<br>PROJECTS TO BE CARRIED OUT</h2>
  <ul class="abs bullets" style="left:626px;top:2056px;width:440px">
    <li>Adapt accessibility to certain places tourist or cultural.</li>
    <li>Advise various players in the sector tourism and culture for the reception of people with disabilities.</li>
    <li>Provide interpreters for various events .</li>
    <li>Creation of a platform bringing together tourist sites, accommodation and activities adapted from the Dents du Midday.</li>
  </ul>
  <a class="btn" style="left:609px;top:2334px;height:42px">READ MORE</a>

  <div class="abs big-num" style="left:10px;top:2480px">03</div>
  <h2 class="abs heading" style="left:142px;top:2589px">LATEST EVENTS</h2>
  <div class="abs arrows">
    <span><svg width="14" height="14"><path d="M9 2 L4 7 L9 12" stroke="#333" stroke-width="2" fill="none"/></svg></span>
    <span><svg width="14" height="14"><path d="M5 2 L10 7 L5 12" stroke="#333" stroke-width="2" fill="none"/></svg></span>
  </div>
  <div class="abs event-card" role="img" aria-label="Photo of a crowd in red costumes gathered on a town street">
    <div class="date">09 JUNE 2022</div>
    <div class="ttl">SED UT PERSPICIATIS UNDE OMNIS ISTE</div>
    <div class="sub">Lorem ipsum dolor sit amet, consectetur adipiscin</div>
    <div class="plus">+</div>
  </div>

  <div class="event-item" style="top:2693px">
    <div class="box"><h4>SED UT PERSPICIATIS UNDE OMNIS ISTE</h4><p>Lorem ipsum dolor sit amet, consectetur adipiscing elit,<br>sed do eiusmod tempor incididunt ut labore et dolore</p></div>
    <svg class="diamond" viewBox="0 0 92 92"><polygon points="46,0 92,46 46,92 0,46" fill="#e0141e" stroke="#fff" stroke-width="3"/></svg>
    <div class="day">09<br>JUN</div>
  </div>
  <div class="event-item" style="top:2830px">
    <div class="box"><h4>SED UT PERSPICIATIS UNDE OMNIS ISTE</h4><p>Lorem ipsum dolor sit amet, consectetur adipiscing elit,<br>sed do eiusmod tempor incididunt ut labore et dolore</p></div>
    <svg class="diamond" viewBox="0 0 92 92"><polygon points="46,0 92,46 46,92 0,46" fill="#e0141e" stroke="#fff" stroke-width="3"/></svg>
    <div class="day">09<br>JUN</div>
  </div>
  <div class="event-item" style="top:2967px">
    <div class="box"><h4>SED UT PERSPICIATIS UNDE OMNIS ISTE</h4><p>Lorem ipsum dolor sit amet, consectetur adipiscing elit,<br>sed do eiusmod tempor incididunt ut labore et dolore</p></div>
    <svg class="diamond" viewBox="0 0 92 92"><polygon points="46,0 92,46 46,92 0,46" fill="#e0141e" stroke="#fff" stroke-width="3"/></svg>
    <div class="day">09<br>JUN</div>
  </div>

  <svg class="abs" style="left:0;top:3110px" width="1200" height="800" viewBox="0 3110 1200 800">
    <defs>
      <linearGradient id="collageTone" x1="0" y1="1" x2="1" y2="0">
        <stop offset="0" stop-color="#a0703e"/>
        <stop offset="0.5" stop-color="#b98e6c"/>
        <stop offset="1" stop-color="#d3cbc4"/>
      </linearGradient>
    </defs>
    <polygon points="0,3121 1200,3170 1200,3705 500,3705 0,3895" fill="#d8141d"/>
    <polygon role="img" aria-label="Photo collage of a wheelchair user at sunset and people celebrating outdoors" points="65,3290 65,3790 520,3790 720,3620 560,3290" fill="url(#collageTone)"/>
  </svg>
  <div class="abs big-num" style="left:860px;top:3500px;color:rgba(255,255,255,0.08)">04</div>
  <div class="abs member">
    <h3>ANNUAL MEMBERSHIP FEE</h3>
    <p>CHF 50.- / ADULT</p>
    <p>CHF 80.- / COUPLE</p>
    <h3 style="margin-top:6px">ANNUAL CONTRIBUTION OF<br>BENEFACTOR MEMBER:</h3>
    <p>FROM 80.</p>
    <p>FOR DONATIONS, PLEASE REGISTER</p>
    <p>THE ANNOTATION "GIFT</p>
  </div>
  <a class="btn" style="left:760px;top:3594px;height:40px;background:#1a1a1a">READ MORE</a>

  <div class="abs" role="img" aria-label="Faint photo of a person wearing headphones" style="left:640px;top:3820px;width:560px;height:484px;background:linear-gradient(160deg,#f7f7f7,#eeeeee 60%,#f6f6f6)"></div>
  <div class="abs big-num" style="left:335px;top:3760px">05</div>
  <h2 class="abs heading" style="left:506px;top:3890px">CONTACT US</h2>
  <div class="field" style="left:170px;top:3979px;width:278px;height:46px">Enter Name</div>
  <div class="field" style="left:460px;top:3979px;width:278px;height:46px">Enter Email</div>
  <div class="field" style="left:751px;top:3979px;width:278px;height:46px">Enter Phone</div>
  <div class="field" style="left:170px;top:4037px;width:859px;height:100px">Message</div>
  <a class="btn" style="left:506px;top:4175px;height:40px">SUBMIT MESSAGE</a>

  <footer class="abs footer">
    <div class="brand"><span class="mark" style="background:#fff"></span>OpenPath Association</div>
    <div class="addr">
      <svg width="14" height="18" viewBox="0 0 14 18"><path d="M7 0C3 0 0 3 0 7c0 5 7 11 7 11s7-6 7-11c0-4-3-7-7-7z" fill="#fff"/><circle cx="7" cy="7" r="2.5" fill="#2c2c2e"/></svg>
      Meadow Lane 12, 1870 Valmont
      <span class="social"><span></span><span style="background:#22a4e6"></span><span style="background:#1c5fa8"></span></span>
    </div>
    <div class="copy">Copyright 2022 OpenPath Association All Rights Reserved &nbsp;|&nbsp; Privacy Policy</div>
  </footer>

</div>
</body>
</html>
```